MRT Property - Business Cards

Looking for a business card & general letterhead, signage etc design for our new logo.

Colours:
000a20
0056a2
00b5ef
0088ce
68cef2

Fonts:
Poppins
Karla

Please keep look and feel of new brand - example in the zip package I sent.

```html
<!DOCTYPE html>
<html lang="en">
<head>
<meta charset="utf-8">
<title>MRT Property – Business Cards</title>
<link href="https://fonts.googleapis.com/css2?family=Poppins:wght@300;400;500;700&display=swap" rel="stylesheet">
<style>
  :root {
    --navy: #0d1226;
    --navy-deep: #000a20;
    --blue: #0056a2;
    --blue-mid: #0088ce;
    --cyan: #00b5ef;
    --sky: #68cef2;
    --white: #ffffff;
    --stage: #e9ebef;
  }
  * { box-sizing: border-box; margin: 0; padding: 0; }
  html, body { width: 1200px; height: 780px; overflow: hidden; }
  body {
    background: var(--stage);
    font-family: "Poppins", sans-serif;
    position: relative;
  }
  .card {
    position: absolute;
    top: 240px;
    width: 520px;
    height: 300px;
    border-radius: 22px;
    background: var(--navy);
    overflow: hidden;
    box-shadow: 0 10px 28px rgba(0, 10, 32, 0.25);
  }
  .card--front { left: 50px; }
  .card--back { left: 630px; }

  /* front */
  .brand {
    position: absolute;
    left: 40px;
    top: 100px;
    width: 190px;
    display: flex;
    align-items: center;
    gap: 10px;
  }
  .brand__dot {
    width: 22px; height: 22px;
    border-radius: 50%;
    background: var(--sky);
    flex: none;
  }
  .brand__name {
    font-weight: 700;
    font-size: 25px;
    line-height: 1.1;
    color: var(--blue-mid);
  }
  .divider {
    position: absolute;
    left: 240px;
    top: 70px;
    width: 80px;
    height: 150px;
  }
  .person {
    position: absolute;
    left: 300px;
    top: 92px;
    color: var(--white);
  }
  .person__name {
    font-size: 25px;
    line-height: 1;
    color: var(--sky);
    font-weight: 300;
  }
  .person__name strong { color: var(--blue-mid); font-weight: 700; }
  .person__role {
    font-size: 11px;
    font-weight: 500;
    margin-top: 4px;
  }
  .contacts {
    list-style: none;
    margin-top: 14px;
    font-size: 12.5px;
    font-weight: 300;
  }
  .contacts li {
    display: flex;
    align-items: center;
    gap: 8px;
    margin-bottom: 5px;
  }
  .contacts svg { width: 12px; height: 12px; flex: none; }
  .address {
    position: absolute;
    left: 22px;
    bottom: 22px;
    font-size: 11px;
    font-weight: 400;
    color: var(--white);
  }
  .edge-band {
    position: absolute;
    left: 0; right: 0; bottom: 0;
    height: 14px;
    display: flex;
  }
  .edge-band__light { width: 42%; background: var(--sky); }
  .edge-band__dark { flex: 1; background: var(--blue); }

  /* back */
  .pattern {
    position: absolute;
    inset: 0;
    background: linear-gradient(200deg, var(--blue-mid) 0%, #1d2f8a 35%, var(--navy) 75%);
    opacity: 0.55;
  }
  .back-brand {
    position: absolute;
    right: 40px;
    bottom: 34px;
    display: flex;
    align-items: center;
    gap: 6px;
  }
  .back-brand__dot {
    width: 10px; height: 10px;
    border-radius: 50%;
    background: var(--sky);
  }
  .back-brand__name {
    font-size: 13px;
    font-weight: 700;
    color: var(--blue-mid);
  }
</style>
</head>
<body>

<section class="card card--front">
  <div class="brand">
    <span class="brand__dot"></span>
    <span class="brand__name">MRT Property</span>
  </div>

  <svg class="divider" viewBox="0 0 80 150" aria-hidden="true">
    <line x1="75" y1="2" x2="5" y2="148" stroke="#0056a2" stroke-width="1.2"/>
  </svg>

  <div class="person">
    <p class="person__name"><strong>Liam</strong> Porter</p>
    <p class="person__role">Director</p>
    <ul class="contacts">
      <li>
        <svg viewBox="0 0 12 12" aria-hidden="true"><circle cx="6" cy="6" r="6" fill="#68cef2"/><path d="M4 3.2c.4-.3.8-.2 1 .2l.4.8c.1.3 0 .5-.2.7l-.3.3c.3.7.8 1.2 1.5 1.5l.3-.3c.2-.2.4-.3.7-.2l.8.4c.4.2.5.6.2 1-.5.6-1.2.8-2 .4C5 7.5 4.5 7 4 5.8c-.4-.9-.5-2 0-2.6z" fill="#0d1226"/></svg>
        +61 2 9000 1234
      </li>
      <li>
        <svg viewBox="0 0 12 12" aria-hidden="true"><circle cx="6" cy="6" r="6" fill="#68cef2"/><circle cx="6" cy="6" r="3.5" fill="none" stroke="#0d1226" stroke-width=".8"/><path d="M2.5 6h7M6 2.5c-1.3 1.8-1.3 5.2 0 7M6 2.5c1.3 1.8 1.3 5.2 0 7" fill="none" stroke="#0d1226" stroke-width=".7"/></svg>
        www.mrtproperty.com.au
      </li>
      <li>
        <svg viewBox="0 0 12 12" aria-hidden="true"><circle cx="6" cy="6" r="6" fill="#68cef2"/><rect x="3" y="4" width="6" height="4.2" fill="none" stroke="#0d1226" stroke-width=".8"/><path d="M3 4l3 2.3L9 4" fill="none" stroke="#0d1226" stroke-width=".8"/></svg>
        info@mrtproperty.com.au
      </li>
    </ul>
  </div>

  <p class="address">Suite 4.12, Level 3, 18 Harbour Lane, Riverside Park NSW 2199</p>

  <div class="edge-band">
    <span class="edge-band__light"></span>
    <span class="edge-band__dark"></span>
  </div>
</section>

<section class="card card--back">
  <div class="pattern" role="img" aria-label="Repeating brand pattern fading from bright blue at the top right to dark navy"></div>
  <div class="back-brand">
    <span class="back-brand__dot"></span>
    <span class="back-brand__name">MRT Property</span>
  </div>
</section>

</body>
</html>
```